PSD Designs needed to give to my Developer

Hello, I need PSD files to give to my programmer for the creation of my new website. The website is for KORVA lane, a new clothing company based in Chicago, IL. We sell womens, mens and kids fashion. We specialize in jackets, outerwear and sweaters, but we sell clothing from every category, I have someone working on the logo, so I can't include it for reference. However, I have included 2 reference sites as well as a PDF of how the 2 reference sites could be merged together. The main company color should be blue (hence the name KORVA lane), and the overall feel of the site should be FUN. It should communicate: This is where you want to shop if you want a FUN, HAPPY experience. I need the Home Page file designed very quickly. Whoever is awarded this job will immediately continue working with me to design the other 8 pages. I will pay for all pages. The amount I am offering is for this one page only, and I will pay you additional to design all other 8 pages. Thank you for your time and I will be picking the best design so that we can immediately build a great relationship and work through the rest of the project.

Industry/Entity Type

Apparel Store

Number of Pages Required

1 page

Font styles to use
Sans Serif

Colors
33a6d7
0492cd
ffffff

Requirements
Must have
• I have included all notes in the project description so please check there. My project must communicate: Fun and Happy Design. Even tho I have chosen a few variations of blue below, I still want the designer to incorporate other colors as necessary to acheive the desired look.
Should not have
• It should have a boring, childish feel

```html
<!DOCTYPE html>
<html lang="en">
<head>
<meta charset="utf-8">
<title>KORVA LANE — Home</title>
<link rel="stylesheet" href="https://fonts.googleapis.com/css2?family=Quicksand:wght@400;500;600;700&display=swap">
<style>
  :root {
    --blue: #0492cd;
    --blue-light: #33a6d7;
    --blue-overlay: rgba(51,166,215,0.92);
    --white: #ffffff;
    --ink: #3a3a3a;
    --muted: #9a9a9a;
    --card-bg: #ececec;
    --rule: #e3e3e3;
  }
  * { margin: 0; padding: 0; box-sizing: border-box; }
  html, body { width: 1040px; height: 1200px; overflow: hidden; background: var(--white); }
  body { position: relative; font-family: "Quicksand", sans-serif; color: var(--ink); }

  .promo { position: absolute; left: 140px; top: 14px; font-size: 11px; line-height: 17px; color: #555; }
  .promo strong { font-size: 13px; font-weight: 700; color: #444; }
  .brand { position: absolute; left: 0; width: 1040px; top: 16px; text-align: center;
           font-size: 29px; font-weight: 700; letter-spacing: 3px; color: var(--blue); }
  .account { position: absolute; top: 14px; font-size: 11px; color: #555; text-align: center; }
  .account svg { display: block; margin: 5px auto 0; }
  .account--join { left: 771px; }
  .account--bag { left: 834px; }

  .main-nav { position: absolute; left: 0; top: 74px; width: 1040px; height: 34px; background: var(--blue);
              display: flex; justify-content: center; align-items: center; }
  .main-nav ul { list-style: none; display: flex; align-items: center; height: 34px; margin-left: -5px; }
  .main-nav li { font-size: 11.5px; color: var(--white); letter-spacing: 0.5px; display: flex; align-items: center; height: 100%; }
  .main-nav li.sep { padding: 0 14px; font-size: 10px; }
  .main-nav li.active { background: var(--blue-light); padding: 0 20px; height: 31px; margin-top: 3px; margin-right: 11px; }

  .hero { position: absolute; left: 0; top: 108px; width: 1040px; height: 448px;
          background: linear-gradient(100deg, #9b8a85 0%, #c9cfd6 30%, #4c79b0 50%, #cfd6de 70%, #3650a0 100%); }
  .hero__title { position: absolute; top: 189px; width: 100%; text-align: center; font-size: 12.5px;
                 font-weight: 700; letter-spacing: 1px; color: var(--white); }
  .btn { display: block; width: 131px; height: 37px; line-height: 37px; text-align: center; background: var(--blue);
         color: var(--white); font-size: 11.5px; font-weight: 700; letter-spacing: 0.6px; }
  .hero .btn { position: absolute; left: 455px; top: 216px; }
  .hero__dots { position: absolute; top: 424px; left: 495px; display: flex; gap: 5px; }
  .hero__dots span { width: 9px; height: 9px; border: 1.5px solid var(--white); border-radius: 50%; }
  .hero__dots span.on { background: var(--white); }

  .section-title { position: absolute; top: 601px; width: 1040px; text-align: center; font-size: 14px;
                   font-weight: 600; letter-spacing: 2px; color: var(--blue); }
  .product { position: absolute; top: 647px; width: 239px; height: 145px; background: var(--card-bg); }
  .product__photo { position: absolute; left: 50px; right: 50px; top: 0; bottom: 0;
                    background: linear-gradient(#7a8590, #4a4f56); }
  .product__overlay { position: absolute; left: 10px; right: 10px; top: 11px; height: 124px; background: var(--blue-overlay); }
  .product__label { position: absolute; left: 50%; top: 50%; transform: translate(-50%,-50%); width: 123px; height: 36px;
                    border: 2px solid var(--white); color: var(--white); font-size: 11px; font-weight: 700;
                    letter-spacing: 0.7px; text-align: center; line-height: 32px; }
  .products-cta { position: absolute; left: 455px; top: 817px; }

  .newsletter-bg { position: absolute; left: 0; top: 894px; width: 1040px; height: 132px;
                   background: linear-gradient(90deg, #3d3d40, #5a5552 50%, #3a3a3a); }
  .newsletter { position: absolute; left: 298px; top: 986px; width: 446px; height: 92px; background: var(--blue); }
  .newsletter h2 { margin-top: 17px; text-align: center; font-size: 15px; font-weight: 400; letter-spacing: 0.6px; color: var(--white); }
  .newsletter form { position: absolute; left: 100px; top: 41px; width: 266px; height: 32px; background: var(--white); display: flex; }
  .newsletter input { flex: 1; border: 0; padding-left: 14px; font-family: inherit; font-size: 9.5px; font-style: italic; color: var(--muted); background: transparent; }
  .newsletter button { width: 100px; margin: 2px; border: 0; background: var(--blue-light); color: var(--white);
                       font-family: inherit; font-size: 11.5px; font-weight: 700; letter-spacing: 0.4px; }

  .site-footer { position: absolute; left: 0; top: 1131px; width: 1040px; border-top: 1px solid var(--rule); height: 69px; }
  .copyright { position: absolute; left: 142px; top: 14px; font-size: 11px; font-weight: 700; letter-spacing: 0.4px; color: #333; }
  .footer-links { position: absolute; right: 141px; top: 14px; display: flex; list-style: none; font-size: 11.5px; letter-spacing: 0.4px; color: #333; }
  .footer-links li.sep { padding: 0 11px; font-size: 10px; }
</style>
</head>
<body>
  <header class="site-header">
    <p class="promo">Pop-up your own KORVA<br>Boulevard for ONLY <strong>$99</strong></p>
    <div class="brand">KORVA LANE</div>
    <a class="account account--join">Join Now
      <svg width="16" height="16" viewBox="0 0 16 16"><circle cx="8" cy="8" r="7" fill="none" stroke="#555" stroke-width="1"/><path d="M3 8h8M8 5l3 3-3 3" fill="none" stroke="#555" stroke-width="1"/></svg>
    </a>
    <a class="account account--bag">Shoping Bag
      <svg width="16" height="16" viewBox="0 0 16 16"><path d="M5 6V4a3 3 0 0 1 6 0v2" fill="none" stroke="#444" stroke-width="1.4"/><path d="M1 6h14l-2 9H3z" fill="#444"/></svg>
    </a>
  </header>

  <nav class="main-nav">
    <ul>
      <li class="active">HOME</li>
      <li>GET TO KNOW US</li><li class="sep">I</li>
      <li>WHY KORVA?</li><li class="sep">I</li>
      <li>HOST A POP-UP</li><li class="sep">I</li>
      <li>BECOME A STYLIST</li>
    </ul>
  </nav>

  <section class="hero" role="img" aria-label="Three smiling women in colourful winter layers and scarves walking outdoors among bare trees">
    <h1 class="hero__title">FAMILY OF THREE</h1>
    <a class="btn">Shop Now</a>
    <div class="hero__dots"><span></span><span></span><span></span><span class="on"></span></div>
  </section>

  <h2 class="section-title">OUR MAIN PRODUCTS</h2>

  <div class="product" style="left:141px">
    <div class="product__photo" role="img" aria-label="Man wearing a dark jacket"></div>
    <div class="product__overlay"><span class="product__label">JACKETS</span></div>
  </div>
  <div class="product" style="left:400px">
    <div class="product__photo" role="img" aria-label="Man wearing a long outerwear coat"></div>
    <div class="product__overlay"><span class="product__label">OUTERWEAR</span></div>
  </div>
  <div class="product" style="left:659px">
    <div class="product__photo" role="img" aria-label="Man wearing a knit sweater"></div>
    <div class="product__overlay"><span class="product__label">SWEATERS</span></div>
  </div>
  <a class="btn products-cta">Shop Now</a>

  <div class="newsletter-bg" role="img" aria-label="Young man relaxing in a modern room with geometric wall art, darkened"></div>
  <section class="newsletter">
    <h2>ENTER YOUR EMAIL ADDRESS</h2>
    <form>
      <input type="email" placeholder="EMAIL ADDRESS">
      <button type="button">Subscribe</button>
    </form>
  </section>

  <footer class="site-footer">
    <p class="copyright">© 2018 Korvalane. All Rights Reserved.</p>
    <ul class="footer-links">
      <li>Terms</li><li class="sep">I</li>
      <li>Sitemap</li><li class="sep">I</li>
      <li>Privacy</li><li class="sep">I</li>
      <li>Policy</li><li class="sep">I</li>
      <li>Join our Network</li>
    </ul>
  </footer>
</body>
</html>
```